Modern Business Card For A Digital Advertising Company

I'll be print on the Pell Prints Velour paper http://us.pellprints.com/products/velour/business-cards.html
Need's to be modern and use the color palette of the logo or gray scales. I think integrating the pixelation of the logo in to the card and having it wrap from one side to the other could be interesting. My company provides ad operations, web development, and number of other services to websites around the world. You can see my website at http://www.zantorhq.com
Contact info on the card needs to have
Owen Lasko
President
p.318.204.6637
owen@zantorhq.com
http://www.zantorhq.com
Doesn't necessarily need to be in that order
Website owners
Business

```html
<!DOCTYPE html>
<html lang="en">
<head>
<meta charset="utf-8">
<title>Zantor HQ — Business Card</title>
<link rel="stylesheet" href="https://fonts.googleapis.com/css2?family=Questrial&family=Open+Sans:wght@700&display=swap">
<style>
  :root {
    --stage: #2e2f30;
    --paper: #ffffff;
    --green-light: #8dc63f;
    --green-dark: #5b8a39;
    --charcoal: #3b3b3b;
    --ink: #4a4a4a;
    --white: #ffffff;
  }
  * { margin: 0; padding: 0; box-sizing: border-box; }
  html, body {
    width: 1200px; height: 450px; overflow: hidden;
    background: var(--stage);
  }
  .canvas { position: relative; width: 1200px; height: 450px; }

  .card {
    position: absolute; top: 74px;
    width: 525px; height: 301px; overflow: hidden;
  }
  .card--front { left: 57px; background: var(--paper); }
  .card--back {
    left: 621px;
    background: linear-gradient(90deg, var(--green-light) 0%, var(--green-dark) 100%);
  }

  .front-waves { position: absolute; inset: 0; width: 525px; height: 301px; }

  .brand {
    position: absolute; display: flex; align-items: center; gap: 8px;
    font-family: "Open Sans", sans-serif; font-weight: 700;
    letter-spacing: 1px; text-transform: uppercase;
  }
  .brand__mark { display: block; }
  .brand--front { left: 68px; top: 118px; font-size: 24px; color: var(--green-light); }
  .brand--front .brand__mark { width: 16px; height: 16px; background: var(--green-light); }
  .brand--back {
    left: 0; right: 0; top: 100px; justify-content: center;
    font-size: 44px; color: var(--white); gap: 14px;
  }
  .brand--back .brand__mark { width: 30px; height: 30px; background: var(--white); }

  .contact {
    position: absolute; left: 268px; top: 87px; list-style: none;
    font-family: "Questrial", sans-serif; font-size: 15px; color: var(--ink);
  }
  .contact__item { display: flex; align-items: center; gap: 6px; height: 22px; }
  .contact__icon { width: 10px; height: 10px; flex: none; }

  .signature {
    position: absolute; left: 258px; top: 262px;
    color: var(--white); white-space: nowrap;
  }
  .signature__name { font-family: "Open Sans", sans-serif; font-weight: 700; font-size: 18px; }
  .signature__title { font-family: "Questrial", sans-serif; font-size: 15px; margin-left: 2px; }

  .back-url {
    position: absolute; left: 0; right: 0; top: 242px; text-align: center;
    font-family: "Questrial", sans-serif; font-size: 20px; letter-spacing: 1px;
    color: var(--white);
  }
</style>
</head>
<body>
<main class="canvas">

  <section class="card card--front" aria-label="Card front">
    <svg class="front-waves" viewBox="0 0 525 301" aria-hidden="true">
      <defs>
        <linearGradient id="greenBand" x1="0" y1="0" x2="1" y2="0">
          <stop offset="0" stop-color="#8dc63f"/>
          <stop offset="1" stop-color="#5b8a39"/>
        </linearGradient>
      </defs>
      <path d="M0,150 C15,215 70,252 170,256 C270,260 330,236 400,238 C460,240 500,262 525,292 L525,301 L0,301 Z" fill="url(#greenBand)"/>
      <path d="M14,160 C45,228 115,250 205,244 C300,238 360,214 420,220 C470,226 505,258 525,290 L525,276 C500,240 460,210 410,208 C350,205 300,230 205,236 C115,242 50,218 14,160 Z" fill="#3b3b3b"/>
    </svg>

    <div class="brand brand--front"><span class="brand__mark"></span>Zantor HQ</div>

    <ul class="contact">
      <li class="contact__item">
        <svg class="contact__icon" viewBox="0 0 10 10" aria-hidden="true"><path d="M2,1 L4,1 L4.6,3.2 L3.4,4.2 C4,5.6 4.6,6.2 5.8,6.6 L6.8,5.4 L9,6 L9,8 C9,8.6 8.6,9 8,9 C4.2,8.8 1.2,5.8 1,2 C1,1.4 1.4,1 2,1 Z" fill="#5b8a39"/></svg>
        318.204.6637
      </li>
      <li class="contact__item">
        <svg class="contact__icon" viewBox="0 0 10 10" aria-hidden="true"><circle cx="5" cy="5" r="5" fill="#5b8a39"/><rect x="2.3" y="3.3" width="5.4" height="3.6" fill="#fff"/><path d="M2.3,3.3 L5,5.4 L7.7,3.3" stroke="#5b8a39" stroke-width="0.7" fill="none"/></svg>
        owen@zantorhq.com
      </li>
      <li class="contact__item">
        <svg class="contact__icon" viewBox="0 0 10 10" aria-hidden="true"><circle cx="5" cy="5" r="5" fill="#5b8a39"/><path d="M1,5 H9 M5,1 C3,3 3,7 5,9 M5,1 C7,3 7,7 5,9" stroke="#fff" stroke-width="0.7" fill="none"/></svg>
        www.zantorhq.com
      </li>
    </ul>

    <p class="signature"><span class="signature__name">Owen Lasko,</span><span class="signature__title"> President</span></p>
  </section>

  <section class="card card--back" aria-label="Card back">
    <div class="brand brand--back"><span class="brand__mark"></span>Zantor HQ</div>
    <p class="back-url">www.zantorhq.com</p>
  </section>

</main>
</body>
</html>
```